Quarrybend Marble & Tile Needs a Business Card

Attached you will find your logo, my photo and design guidelines for a new business card. The final design will need two separate files to create an embossed card. The cards will be printed by www.plinkprint.com (Instructions below)
Format is the Plink SQUARE card
Quarrybend Marble And Tile is a brick and mortar, retail stone and tile shop.
One the front:
Quarrybend Marble And Tile
Dorian Fesslock
Owner
24807 Hollis Verdant Blvd
Suite P & R
Charlotte, NC 28193
Cell: 704-583-7142
Web: www.QuarrybendMarbleAndTile.com
(Make each word of the domain a different or alternating color)
On the back;
Something that shows beautiful colorful tile
Follow the design guide closely please. For more information see this page that describes creating the spot gloss file: https://www.plinkprint.com/us/business-cards/design-guidelines-spot-gloss
The logo is what we would like to have raised spot glossed.
Format is the Plink SQUARE card. See attahced guidlines.

```html
<!DOCTYPE html>
<html lang="en">
<head>
<meta charset="utf-8">
<title>Quarrybend Marble &amp; Tile – Business Card</title>
<link rel="stylesheet" href="https://fonts.googleapis.com/css2?family=Cinzel:wght@400&family=Tinos&family=Montserrat:wght@400;500&display=swap">
<style>
  :root {
    --stage: #8a8b8e;
    --navy: #22313e;
    --emboss: #3f5465;
    --ink: #1d242b;
    --rust: #9a3a14;
    --ochre: #c08a2c;
    --slate: #6c7a6a;
    --paper: #ffffff;
  }
  * { margin: 0; padding: 0; box-sizing: border-box; }
  html, body { width: 900px; height: 1200px; overflow: hidden; }
  body { background: var(--stage); position: relative; font-family: "Montserrat", sans-serif; }

  .card {
    position: absolute;
    left: 135px;
    width: 631px;
    border-radius: 12px;
  }
  .card-back { top: 215px; height: 357px; background: var(--navy); }
  .card-front { top: 628px; height: 359px; background: var(--paper); }

  .wordmark { font-family: "Cinzel", serif; font-weight: 400; text-align: center; }
  .card-back .wordmark {
    position: absolute; left: 0; right: 0; top: 138px;
    color: var(--emboss); font-size: 40px; letter-spacing: 5px; line-height: 1.1;
  }
  .card-back .wordmark span { display: block; font-size: 17px; letter-spacing: 9px; margin-top: 6px; }

  .portrait {
    position: absolute; left: 28px; top: 29px; width: 90px; height: 90px;
    background: linear-gradient(160deg, #4a4a4e, #2a2c31);
    border: 2px solid var(--ochre);
  }

  .card-front .wordmark {
    position: absolute; right: 30px; top: 44px; text-align: right;
    color: var(--ink); font-size: 27px; letter-spacing: 3px; line-height: 1.1;
  }
  .card-front .wordmark span { display: block; font-size: 13px; letter-spacing: 6px; margin-top: 6px; }

  .person { position: absolute; left: 30px; top: 194px; }
  .person-name { font-family: "Tinos", serif; font-size: 25px; color: var(--ink); line-height: 1.1; }
  .person-role { font-size: 14px; color: var(--rust); margin-top: 1px; }

  .tile-band {
    position: absolute; left: 30px; right: 30px; top: 250px; height: 3px;
    background: repeating-linear-gradient(90deg, var(--ink) 0 30px, var(--rust) 30px 60px);
  }

  .contact { position: absolute; left: 30px; top: 264px; list-style: none; font-size: 15px; color: var(--ink); }
  .contact li { display: flex; align-items: center; height: 24.5px; }
  .contact svg { width: 14px; height: 14px; margin-right: 6px; fill: var(--rust); }
  .contact .phone { letter-spacing: 2px; }
  .w1 { color: var(--rust); }
  .w2 { color: var(--ochre); }
  .w3 { color: var(--slate); }

  .address {
    position: absolute; right: 30px; top: 264px; text-align: right;
    font-style: normal; font-size: 15px; color: var(--ink); line-height: 24.5px;
  }
</style>
</head>
<body>
  <section class="card card-back">
    <div class="wordmark">QUARRYBEND<span>MARBLE &amp; TILE</span></div>
  </section>

  <section class="card card-front">
    <div class="portrait" role="img" aria-label="Portrait photo of the owner"></div>
    <div class="wordmark">QUARRYBEND<span>MARBLE &amp; TILE</span></div>

    <div class="person">
      <p class="person-name">Dorian Fesslock</p>
      <p class="person-role">Owner</p>
    </div>

    <div class="tile-band" role="img" aria-label="Decorative tile pattern band"></div>

    <ul class="contact">
      <li>
        <svg viewBox="0 0 24 24" aria-hidden="true"><path d="M6.6 10.8a15 15 0 0 0 6.6 6.6l2.2-2.2a1 1 0 0 1 1-.25 11.4 11.4 0 0 0 3.6.57 1 1 0 0 1 1 1V20a1 1 0 0 1-1 1A17 17 0 0 1 3 4a1 1 0 0 1 1-1h3.5a1 1 0 0 1 1 1c0 1.25.2 2.45.57 3.57a1 1 0 0 1-.25 1z"/></svg>
        <span class="phone">704-583-7142</span>
      </li>
      <li>
        <svg viewBox="0 0 24 24" aria-hidden="true"><path d="M2 5h20v14H2zm2 2v.5l8 5 8-5V7l-8 5z"/></svg>
        <span>info@<span class="w1">Quarrybend</span><span class="w2">Marble</span><span class="w3">And</span><span class="w2">Tile</span>.com</span>
      </li>
      <li>
        <svg viewBox="0 0 24 24" aria-hidden="true"><path d="M12 2a10 10 0 1 0 0 20 10 10 0 0 0 0-20zm6.9 9h-3a15 15 0 0 0-1.3-5.6A8 8 0 0 1 18.9 11zM12 4.1c.9 1.3 1.8 3.6 1.9 6.9h-3.8c.1-3.3 1-5.6 1.9-6.9zM9.4 5.4A15 15 0 0 0 8.1 11h-3a8 8 0 0 1 4.3-5.6zM5.1 13h3a15 15 0 0 0 1.3 5.6A8 8 0 0 1 5.1 13zm6.9 6.9c-.9-1.3-1.8-3.6-1.9-6.9h3.8c-.1 3.3-1 5.6-1.9 6.9zm2.6-1.3a15 15 0 0 0 1.3-5.6h3a8 8 0 0 1-4.3 5.6z"/></svg>
        <span>www.<span class="w1">Quarrybend</span><span class="w2">Marble</span><span class="w3">And</span><span class="w2">Tile</span>.com</span>
      </li>
    </ul>

    <address class="address">
      24807 Hollis Verdant Blvd<br>
      Suite P &amp; R<br>
      Charlotte, NC 28193
    </address>
  </section>
</body>
</html>
```